Communication and Marketing agency needs a new presentation card

We are a group of communication and marketing agencies specialized in companies that are in the logistics and industrial sector. The head agency is TELVANO Grupo and the group consists of 4 agencies: TELVANO Media, TELVANO Digital, TELVANO Research and DifundeEnPantalla. We hace 4 offices in Spain (Madrid, Barcelona, Valencia and Murcia). We are looking for a clean and attractive design that transmits our experience, brand presence in the market and knowledge to those who receive the card.It has to maintain the colors of the logo that is attached.
Target Market(s)
logistics and industrial sector
Marketing department
Contact Information for Business Card
Clean and attractive design

```html
<!DOCTYPE html>
<html lang="es">
<head>
<meta charset="utf-8">
<title>TELVANO Grupo – Tarjeta de presentación</title>
<link href="https://fonts.googleapis.com/css2?family=Jost:wght@400;500&display=swap" rel="stylesheet">
<style>
  :root {
    --stage: #2a2a2a;
    --paper: #ffffff;
    --brand-red: #b51c28;
    --ink: #4a4a4a;
    --band: #555150;
    --white: #ffffff;
  }
  * { margin: 0; padding: 0; box-sizing: border-box; }
  html, body {
    width: 1125px; height: 1200px; overflow: hidden;
    background: var(--stage);
    font-family: "Jost", sans-serif;
  }
  .card {
    position: absolute; left: 150px; width: 826px; height: 471px;
    overflow: hidden;
  }
  .card--front { top: 98px; background: var(--paper); }
  .card--back { top: 630px; background: var(--brand-red); }

  /* Front */
  .name-ribbon { position: absolute; left: 0; top: 65px; width: 372px; height: 74px; }
  .name-ribbon svg { position: absolute; inset: 0; }
  .holder { position: absolute; left: 52px; top: 5px; color: var(--white); }
  .holder__name { font-size: 31px; font-weight: 400; line-height: 1.15; letter-spacing: 0.5px; }
  .holder__role { font-size: 21px; line-height: 1.1; }

  .front-brand {
    position: absolute; right: 47px; top: 52px; text-align: right;
    color: var(--brand-red); font-weight: 400; line-height: 1;
  }
  .front-brand__name { display: block; font-size: 62px; letter-spacing: 2px; }
  .front-brand__unit { display: block; font-size: 34px; margin-top: 4px; }

  .contacts { position: absolute; left: 52px; top: 249px; list-style: none; }
  .contacts li {
    display: flex; align-items: center; height: 27px;
    font-size: 22px; color: var(--ink); letter-spacing: 0.3px;
  }
  .contacts svg { width: 20px; height: 20px; margin-right: 17px; flex: none; fill: var(--brand-red); }

  .offices {
    position: absolute; left: 0; right: 0; top: 405px; height: 39px;
    background: var(--band); color: var(--white);
    display: flex; align-items: center; padding-left: 52px;
    font-size: 22px; letter-spacing: 0.3px;
  }
  .offices .dot { width: 6px; height: 6px; border-radius: 50%; background: var(--white); margin: 0 15px; }

  /* Back */
  .group-brand {
    position: absolute; left: 0; right: 0; top: 140px;
    display: flex; justify-content: center; color: var(--white);
  }
  .group-brand__lockup { text-align: right; line-height: 1; font-weight: 400; }
  .group-brand__name { display: block; font-size: 88px; letter-spacing: 3px; }
  .group-brand__unit { display: block; font-size: 52px; margin-top: 6px; }

  .agencies {
    position: absolute; left: 30px; right: 30px; top: 375px;
    display: flex; justify-content: space-between; color: var(--white);
  }
  .agency { text-align: right; line-height: 1; font-weight: 400; width: 160px; }
  .agency__name { display: block; font-size: 28px; letter-spacing: 1px; }
  .agency__unit { display: block; font-size: 18px; margin-top: 3px; }
  .agency--stacked { text-align: left; }
  .agency--stacked .agency__name { font-size: 24px; letter-spacing: 0.5px; }
</style>
</head>
<body>

<section class="card card--front" aria-label="Anverso de la tarjeta">
  <div class="name-ribbon">
    <svg viewBox="0 0 372 74" width="372" height="74" aria-hidden="true">
      <polygon points="0,0 325,0 372,74 0,74" fill="var(--brand-red)"/>
    </svg>
    <div class="holder">
      <p class="holder__name">Ramiro Costales</p>
      <p class="holder__role">Director</p>
    </div>
  </div>

  <div class="front-brand">
    <span class="front-brand__name">TELVANO</span>
    <span class="front-brand__unit">Media</span>
  </div>

  <ul class="contacts">
    <li>
      <svg viewBox="0 0 20 20" aria-hidden="true"><path d="M2 7c0-3 4-4 8-4s8 1 8 4v2h-4V7H6v2H2z"/><rect x="4" y="10" width="12" height="8" rx="1.5"/></svg>
      914 372 058
    </li>
    <li>
      <svg viewBox="0 0 20 20" aria-hidden="true"><path d="M6 1h8a1.5 1.5 0 0 1 1.5 1.5v15A1.5 1.5 0 0 1 14 19H6a1.5 1.5 0 0 1-1.5-1.5v-15A1.5 1.5 0 0 1 6 1zm0.5 2.5v11h7v-11z"/></svg>
      671 248 193
    </li>
    <li>
      <svg viewBox="0 0 20 20" aria-hidden="true"><path d="M1 6h18v1l-9 5-9-5z"/><path d="M1 9l9 5 9-5v7H1z"/></svg>
      rcostales@telvano.es
    </li>
    <li>
      <svg viewBox="0 0 20 20" aria-hidden="true"><rect x="2" y="2" width="16" height="16" rx="2"/></svg>
      ramirocostales
    </li>
    <li>
      <svg viewBox="0 0 20 20" aria-hidden="true"><circle cx="10" cy="10" r="8.5"/><path d="M6 5c2 1 3 3 2 5s1 3 2 5" stroke="#fff" stroke-width="1.6" fill="none"/></svg>
      www.telvano.es
    </li>
  </ul>

  <div class="offices">
    <span>Madrid</span><span class="dot"></span>
    <span>Barcelona</span><span class="dot"></span>
    <span>Valencia</span><span class="dot"></span>
    <span>Murcia</span>
  </div>
</section>

<section class="card card--back" aria-label="Reverso de la tarjeta">
  <div class="group-brand">
    <div class="group-brand__lockup">
      <span class="group-brand__name">TELVANO</span>
      <span class="group-brand__unit">Grupo</span>
    </div>
  </div>

  <div class="agencies">
    <div class="agency"><span class="agency__name">TELVANO</span><span class="agency__unit">Digital</span></div>
    <div class="agency"><span class="agency__name">TELVANO</span><span class="agency__unit">Media</span></div>
    <div class="agency"><span class="agency__name">TELVANO</span><span class="agency__unit">Research</span></div>
    <div class="agency agency--stacked"><span class="agency__name">DIFUNDE</span><span class="agency__name">ENPANTALLA</span></div>
  </div>
</section>

</body>
</html>
```